Redesign a embroidery design sales site

I wrote http://www.stitchesbymolo.com in php from scratch over many years. I need a web designer to give us an up today more interactive site.

The entire site is template driven, with a top.php and bottom.php on every page.

I need these pages redesigned. I'll take your css and web html and
adapt them to my code:

http://www.stitchesbymolo.com/products/1

http://www.stitchesbymolo.com/points.php

http://www.stitchesbymolo.com/details/appliquesunbonnetscrosses
(appliquesunbennetcrosses is the name of the set, this will change)

http://www.stitchesbymolo.com/buydesigns/appliquesunbonnetscrosses

http://www.stitchesbymolo.com/votedesigns/appliquesunbonnetscrosses

http://www.stitchesbymolo.com/votingresults

Forgot to mention this, www.stitchesbymolo.com/indexsummary.php it is a home page I made a while ago

Reason: I didn't time this well as with Thanksgiving fell in there. I'll be sending out general comments about all designs soon.

Time's running out... can you please submit a design for:

http://www.stitchesbymolo.com/indexsummary.php

http://www.stitchesbymolo.com/products/page1

http://www.stitchesbymolo.com/details/santafriendsrw

http://www.stitchesbymolo.com/buydesigns/santafriendsrw

and

All designs submitted from here will be put infront of 1000's of people to vote for their fav

Love and kisses ...
MoLO

All designers ... submissions seem to stop ... please submit a new update based on what I said.   The final design will be voted by members of my website

3 designers have not been eliminated... 1 day left to get your design to me for my website users to vote on.   Please carefully read what I want.  No big banners.  Nothing is that requires daily/weekly maintence

Target Market(s)

Major are 50+ female grammas with sewing/embroidery machines

Industry/Entity Type

Embroidery

Requirements
Must have
• I want the interaction of http://quillpatchwork.com. That is a cool site. I would like to see a working mock up rather that this cookie cutter stuff.
Should not have
• Should not have a flash/DHTML big banner on the page. Follow the flow of the site now so I can plug and play into my existing code.

```html
<!DOCTYPE html>
<html lang="en">
<head>
<meta charset="utf-8">
<title>Stitches By MoLO – Embroidery Designs Online</title>
<link rel="stylesheet" href="https://fonts.googleapis.com/css2?family=Courgette&family=Crimson+Text:wght@400;600&display=swap">
<style>
  :root{
    --cream:#fcebd8;
    --cream-light:#fff6ec;
    --red:#c8121a;
    --red-dark:#9c0c10;
    --orange:#e25b12;
    --gold:#f6c21a;
    --gold-dark:#d89a06;
    --ink:#3a2a20;
    --muted:#6b5a4c;
    --pink-btn:#f08a8f;
    --panel:#232221;
    --panel-line:#3a3836;
    --white:#ffffff;
  }
  *{box-sizing:border-box;margin:0;padding:0}
  html,body{width:1084px;height:1200px;overflow:hidden}
  body{
    background:radial-gradient(ellipse at 50% 30%,var(--cream-light),var(--cream) 70%);
    font-family:"Crimson Text",Georgia,serif;color:var(--ink);position:relative;
  }

  /* top bar */
  .topbar{height:22px;background:linear-gradient(var(--red),var(--red-dark));color:var(--white);
    font-size:9px;display:flex;align-items:center;justify-content:space-between;padding:0 155px}
  .topbar .social{display:flex;gap:6px}
  .topbar .social span{width:9px;height:9px;background:var(--white);opacity:.9;border-radius:2px}
  .topbar nav{display:flex;gap:12px}

  /* header */
  .header{position:relative;height:96px}
  .brand{position:absolute;left:155px;top:38px;font-family:"Crimson Text",Georgia,serif;font-weight:600;font-size:30px;color:var(--red);display:flex;align-items:center;gap:10px}
  .brand .mark{width:14px;height:14px;background:var(--red);border-radius:50%}
  .stats{position:absolute;left:767px;top:24px;font-size:16px;line-height:17px;color:var(--ink)}
  .stats small{display:block;font-size:9px;line-height:14px}
  .stats small b{color:var(--orange);font-weight:600}

  /* nav ribbon */
  .ribbon{position:absolute;top:118px;left:112px;width:861px;height:42px}
  .ribbon svg{position:absolute;left:0;top:0}
  .mainnav{position:absolute;left:32px;right:32px;top:0;height:40px;
    background:linear-gradient(#ffe46a,var(--gold) 60%,var(--gold-dark));display:flex;align-items:center;justify-content:center;
    box-shadow:0 2px 3px rgba(0,0,0,.2)}
  .mainnav a{font-family:"Courgette",cursive;font-size:15px;color:var(--red);text-decoration:none;padding:0 10px;position:relative;height:40px;line-height:38px}
  .mainnav a+a::before{content:"";position:absolute;left:-2px;top:18px;width:4px;height:4px;border-radius:50%;background:var(--red)}
  .mainnav a.active{background:var(--white);color:var(--orange);box-shadow:inset 0 -3px 0 var(--gold)}

  .wrap{position:absolute;left:155px;width:774px}

  /* hero */
  .welcome{top:158px;height:190px;background:radial-gradient(ellipse at 45% 35%,#ee2a48,#c3102b 55%,#8e0a1b);color:var(--white);text-align:center;padding:26px 40px 0}
  .welcome h1{font-family:"Courgette",cursive;font-weight:400;font-size:28px;color:#5a0d0d;margin-bottom:12px}
  .welcome p{font-size:17px;line-height:23px}
  .welcome a{color:var(--gold);text-decoration:none}

  /* products */
  .section-head{top:370px;height:30px;display:flex;align-items:center}
  .section-head h2{font-family:"Courgette",cursive;font-weight:400;font-size:21px;color:var(--orange);width:330px}
  .pager{display:flex;gap:9px;font-size:12px;align-items:center;color:var(--ink)}
  .pager .step{color:var(--red)}
  .pager .current{background:var(--gold);color:var(--white);padding:0 4px}

  .grid{display:grid;grid-template-columns:repeat(4,130px);gap:6px;height:181px}
  .row1{top:415px}
  .row2{top:619px}
  .card{background:var(--white);text-align:center;padding-top:14px;box-shadow:0 3px 5px rgba(120,70,30,.15);height:181px}
  .card.featured{background:linear-gradient(#fbd9c8,#f2b39a)}
  .thumb{width:92px;height:92px;margin:0 auto 10px;border-radius:50%}
  .card h3{font-weight:600;font-size:11px;color:var(--ink);white-space:nowrap}
  .card .price{font-size:11px;color:var(--muted);margin:2px 0 5px}
  .card .price b{color:var(--red);font-weight:600}
  .cart{display:inline-block;width:70px;height:16px;line-height:16px;border-radius:2px;background:var(--pink-btn);color:var(--white);font-family:"Courgette",cursive;font-size:10px}
  .card.featured .cart{background:var(--red)}

  .promo{position:absolute;width:215px;height:181px}
  .sale{background:radial-gradient(ellipse at 50% 40%,#e0342d,#a10d12);text-align:center;color:var(--white);padding-top:94px}
  .sale h4{font-family:"Courgette",cursive;font-weight:400;font-size:18px;color:var(--gold)}
  .sale p{font-size:11px;line-height:12px}
  .sale .btn{display:inline-block;margin-top:6px;width:140px;height:24px;line-height:24px;background:linear-gradient(#ffe14a,var(--gold-dark));color:var(--red);font-family:"Courgette",cursive;font-size:13px}
  .sale .art{position:absolute;left:62px;top:8px;width:92px;height:80px;border-radius:40%;background:radial-gradient(circle,#f8c63a,#b8860b)}
  .happy{background:linear-gradient(#fbe2d4,#f3c6b0);text-align:center;padding:110px 8px 0;font-size:11px;line-height:13px;color:var(--muted)}
  .happy .art{position:absolute;left:28px;top:10px;width:160px;height:90px;border-radius:8px;background:linear-gradient(120deg,#d8434c,#f5a26a)}
  .flutter{position:absolute;left:889px;top:398px;width:60px;height:52px;border-radius:40%;background:radial-gradient(circle,#f5a623,#b85d0a)}

  /* newsletter */
  .newsletter{top:826px;height:46px;background:linear-gradient(#ffd430,var(--gold-dark));display:flex;align-items:center;white-space:nowrap}
  .newsletter > *{flex:none}
  .newsletter .mail{width:44px;height:46px;background:#1d1d1d;display:flex;align-items:center;justify-content:center}
  .newsletter h5{font-family:"Courgette",cursive;font-weight:400;font-size:16px;color:var(--red);margin-left:14px}
  .newsletter span{font-size:11px;color:var(--ink);margin-left:6px}
  .newsletter .field{width:200px;height:22px;background:var(--white);margin-left:12px;border:1px solid #e0b400}
  .newsletter .go{margin-left:12px;width:74px;height:22px;line-height:22px;text-align:center;background:linear-gradient(#e2331f,#a8150c);color:var(--white);font-family:"Courgette",cursive;font-size:12px}

  /* footer */
  .footer{top:909px;height:206px;background:var(--panel);color:#c9c2ba;display:flex;padding:18px 0 0}
  .footer::after{content:"";position:absolute;left:0;right:0;bottom:-5px;height:6px;
    background:radial-gradient(circle at 5px 0,var(--panel) 4px,transparent 4.5px) 0 0/10px 6px repeat-x}
  .footer h6{font-family:"Courgette",cursive;font-weight:400;font-size:17px;color:var(--white);margin-bottom:12px;white-space:nowrap}
  .col{padding:0 20px;border-right:1px solid var(--panel-line)}
  .col:last-child{border-right:0}
  .categories{width:240px}
  .categories ul{list-style:none;columns:2;column-gap:10px;font-size:11px;line-height:17px}
  .categories li{white-space:nowrap}
  .categories li.on{color:var(--gold);font-weight:600}
  .testimonial{width:310px}
  .testimonial .quote{display:flex;gap:10px}
  .testimonial .photo{width:62px;height:70px;flex:none;background:linear-gradient(#d9b38c,#8b6a4a);border:2px solid #ddd}
  .testimonial p{font-style:italic;font-size:11px;line-height:14px;color:#a59d95}
  .testimonial .name{font-family:"Courgette",cursive;color:var(--gold);font-size:12px;margin-top:8px}
  .dots{display:flex;gap:4px;justify-content:center;margin-top:26px}
  .dots i{width:8px;height:8px;border-radius:50%;background:var(--white)}
  .dots i.off{background:transparent;border:1px solid var(--white)}
  .follow{width:224px}
  .follow .icons{display:flex;gap:4px;margin-bottom:10px}
  .follow .icons span{width:22px;height:22px;border-radius:3px}
  .follow small{display:block;font-size:9px;line-height:11px;color:#8e8780;font-style:italic}
  .follow .safe{font-family:"Courgette",cursive;color:var(--white);font-size:12px;margin:14px 0 6px}
  .badges{display:flex;gap:6px}
  .badges span{width:38px;height:22px;border-radius:2px}

  .footbrand{position:absolute;top:1140px;left:0;width:1084px;text-align:center}
  .footbrand strong{font-family:"Crimson Text",Georgia,serif;font-weight:600;font-size:19px;color:var(--red)}
  .footbrand small{display:block;font-size:8px;color:var(--muted)}
</style>
</head>
<body>

<header>
  <div class="topbar">
    <span>Embroidery Designs Online Since 2002</span>
    <span class="social" aria-label="Social links"><span></span><span></span><span></span><span></span><span></span><span></span></span>
    <nav><span>My Account</span><span>Order Status</span><span>View Cart</span><span>Sign in or Create an account</span></nav>
  </div>
  <div class="header">
    <div class="brand"><span class="mark"></span>Stitches By MoLO</div>
    <div class="stats">23,512 Unique designs online<br>1,656 design sets/packs
      <small>Get a <b>membership</b> and download them all!</small></div>
  </div>
</header>

<div class="ribbon">
  <svg width="861" height="48" viewBox="0 0 861 48" aria-hidden="true">
    <path d="M0 10 H40 V46 H0 L14 28 Z" fill="#d89a06"/>
    <path d="M861 10 H821 V46 H861 L847 28 Z" fill="#d89a06"/>
    <path d="M32 40 L40 46 V40 Z M829 40 L821 46 V40 Z" fill="#9a6a00"/>
  </svg>
  <nav class="mainnav">
    <a href="#">Home</a><a href="#">Search</a><a href="#">Free</a><a href="#" class="active">Top lists</a><a href="#">Designs</a><a href="#">Points</a><a href="#">Supplies</a><a href="#">Articles</a><a href="#">Socialize</a><a href="#">Support</a><a href="#">Contact Us</a>
  </nav>
</div>

<section class="wrap welcome">
  <h1>Welcome to Stitches By MoLO</h1>
  <p>We offer unique machine embroidery designs available for instant download. All of our designs are manually digitized and tested for quality. If you experience any problems on this site, please email <a href="#">customerservice@stitchesbymolo.com</a>. Thanks for stopping by and check back often for new items!</p>
</section>

<div class="wrap section-head">
  <h2>New Embroidery Designs</h2>
  <div class="pager"><span class="step">« Previous</span><span>1</span><span>2</span><span class="current">3</span><span>4</span><span>5</span><span class="step">Next »</span></div>
</div>

<section class="wrap grid row1">
  <article class="card"><div class="thumb" role="img" aria-label="Round embroidered Merry Christmas label" style="background:radial-gradient(circle,#f3d6b5 40%,#9b2a1a 42%)"></div><h3>Merry Christmas label</h3><p class="price">Buy this set for <b>$3.60</b></p><span class="cart">Add to Cart</span></article>
  <article class="card featured"><div class="thumb" role="img" aria-label="Elf girl applique design" style="background:radial-gradient(circle,#f6d8b8,#d43a2c)"></div><h3>Elf Face Girl Applique</h3><p class="price">Buy this set for <b>$2.00</b></p><span class="cart">Add to Cart</span></article>
  <article class="card"><div class="thumb" role="img" aria-label="Leaping tiger embroidery design" style="background:radial-gradient(circle,#f5a640,#fff 70%)"></div><h3>Embroidery design Tiger</h3><p class="price">Buy this set for <b>$3.60</b></p><span class="cart">Add to Cart</span></article>
  <article class="card"><div class="thumb" role="img" aria-label="Girl with little dog embroidery design" style="background:radial-gradient(circle,#e9c8a8,#7a6a9a)"></div><h3>Farm Girl and Puppy</h3><p class="price">Buy this set for <b>$5.00</b></p><span class="cart">Add to Cart</span></article>
</section>
<div class="promo sale" style="top:415px;left:714px">
  <div class="art" role="img" aria-label="Golden Christmas bells"></div>
  <h4>Christmas Set Sale!</h4>
  <p>152 Christmas design sets are on sale<br>$2.00 each!</p>
  <span class="btn">Click here for Sale</span>
</div>
<div class="flutter" role="img" aria-label="Orange butterfly"></div>

<section class="wrap grid row2">
  <article class="card"><div class="thumb" role="img" aria-label="Cartoon cat embroidery design" style="background:radial-gradient(circle,#ffffff 45%,#e44a55 47%,#fff 70%)"></div><h3>Merry Christmas label</h3><p class="price">Buy this set for <b>$3.60</b></p><span class="cart">Add to Cart</span></article>
  <article class="card"><div class="thumb" role="img" aria-label="Santa Claus Merry Christmas badge" style="background:radial-gradient(circle,#f3d9c0,#c5282b 60%,#2e7d3a)"></div><h3>Elf Face Girl Applique</h3><p class="price">Buy this set for <b>$3.60</b></p><span class="cart">Add to Cart</span></article>
  <article class="card"><div class="thumb" role="img" aria-label="Donkey in a holly wreath design" style="background:radial-gradient(circle,#8fa0c8 35%,#2f7a3a 60%,#fff 72%)"></div><h3>Embroidery design Tiger</h3><p class="price">Buy this set for <b>$3.60</b></p><span class="cart">Add to Cart</span></article>
  <article class="card"><div class="thumb" role="img" aria-label="Round Merry Christmas snowflake badge" style="background:radial-gradient(circle,#f3e2c8 35%,#b3202a 38%)"></div><h3>Farm Girl and Puppy</h3><p class="price">Buy this set for <b>$5.00</b></p><span class="cart">Add to Cart</span></article>
</section>
<div class="promo happy" style="top:619px;left:714px">
  <div class="art" role="img" aria-label="Happy Hour ribbon with hot air balloon"></div>
  <p>Any hour can be HAPPY HOUR, check back every hour to see if it's happy hour, 50% off a set during happy hour!</p>
</div>

<section class="wrap newsletter">
  <div class="mail"><svg width="22" height="16" viewBox="0 0 22 16" aria-hidden="true"><rect x="1" y="1" width="20" height="14" fill="none" stroke="#fff" stroke-width="1.6"/><path d="M1 1 L11 9 L21 1" fill="none" stroke="#fff" stroke-width="1.6"/></svg></div>
  <h5>Sign up to our Newsletter</h5>
  <span>for sale announcements, articles and tips every week!</span>
  <div class="field"></div>
  <div class="go">Subscribe</div>
</section>

<footer class="wrap footer">
  <div class="col categories">
    <h6>Categories</h6>
    <ul>
      <li>Modern Designs</li><li>What's New</li><li class="on">Alphabets</li><li>Angels</li><li>Animals/Insects</li><li>Applique</li><li>Baby</li>
      <li>Borders</li><li>Boys</li><li>Clothing/Jewelry</li><li>Education</li><li>Embossed Designs</li><li>Fantasy/Pretend</li><li>Floral - Flowers</li>
    </ul>
  </div>
  <div class="col testimonial">
    <h6>What are our customers saying?</h6>
    <div class="quote">
      <div class="photo" role="img" aria-label="Customer portrait"></div>
      <p>Lorem Ipsum is simply dummy text of the printing and typesetting industry. Lorem Ipsum has been the industry's standard dummy text ever since Lorem Ipsum is simply dummy text of the printing...</p>
    </div>
    <div class="name">Lena Hartwell</div>
    <div class="dots"><i></i><i class="off"></i><i></i></div>
  </div>
  <div class="col follow">
    <h6>Follow us</h6>
    <div class="icons" aria-label="Social links">
      <span style="background:#3b5a98"></span><span style="background:#3ea9e0"></span><span style="background:#d6402f"></span><span style="background:#c8202a"></span><span style="background:#f39221"></span>
    </div>
    <small>Copyright © 2012. Stitches By MoLO.<br>Designed by Fernleaf Studio</small>
    <div class="safe">Certified safe and secure</div>
    <div class="badges"><span style="background:#c8302a"></span><span style="background:#d9b42a"></span><span style="background:#4f9a3a"></span><span style="background:#2f6bb0"></span></div>
  </div>
</footer>

<div class="footbrand"><strong>Stitches By MoLO</strong><small>Embroidery Designs Online Since 2002</small></div>

</body>
</html>
```